Local massage therapist needs some new marketing material

Hi there! I am a massage therapist here in Denver, CO in Alder Bend(shopping and art district) of the city. My business is called Lumo Bodywork of Denver. My practice has an eastern influence and I do reflexology, thai massage and use Chinese herbs, etc. I know all my clients and pay close attention to details. I am also very respectful of tradition and it shows in how I work. I tend to like modern, clean, fun, Asian designs. I am wanting a new business card and brochure. I have a logo and branding for my business that I want used in the design. Currently, the sign for my building is purple and I think my logo was designed to be purple. I will attach pictures of it and can send whatever files are necessary so it can be integrated into the brochure, etc. I like the purple but open to using other colors as well. Thanks!
My website is lumobodyworkofdenver.example where info can be gathered about me and services/fees for brochure.
Updates

Just increased budget. Please see new feedback in discussion thread.

Thanks!

                                       HEY ALL,

Just wanted to let you know that I made a change to my website. It is on the Prices Page. I no longer have the frequent  flyer prices but I added discounts. Let me know if you have any questions. Thanks so much!

Target Market(s)

healthy, urban, educated, upper middle class, yogis

Industry/Entity Type

Marketing

Requirements
Must have
• logo stays purple
Should not have
• not too busy

```html
<!DOCTYPE html>
<html lang="en">
<head>
<meta charset="utf-8">
<title>Lumo Bodywork of Denver – Business Card</title>
<link rel="stylesheet" href="https://fonts.googleapis.com/css2?family=Open+Sans:ital,wght@0,400;0,600;0,700;1,400&display=swap">
<style>
  :root {
    --purple: #5f2d91;
    --purple-soft: #7a4aa8;
    --ink: #4a4a4a;
    --ink-light: #7a7a7a;
    --rule: #3b2a4a;
    --paper: #ffffff;
    --backdrop: #ece8e3;
  }
  * { box-sizing: border-box; margin: 0; padding: 0; }
  html, body {
    width: 1200px; height: 720px; overflow: hidden;
    background: var(--backdrop);
    font-family: "Open Sans", Arial, sans-serif;
  }
  .sheet {
    width: 1200px; height: 720px;
    display: flex; align-items: center; justify-content: center; gap: 40px;
  }
  .card {
    position: relative;
    width: 540px; height: 309px;
    background: var(--paper);
    box-shadow: 0 6px 18px rgba(0,0,0,.12);
    overflow: hidden;
  }

  /* Front */
  .card-front .band {
    position: absolute; left: 0; top: 0; width: 100%; height: 108px;
    background: var(--purple);
    border-bottom: 3px solid var(--rule);
  }
  .brand-name {
    position: absolute; left: 0; right: 0; top: 122px;
    text-align: center;
    font-weight: 400; font-size: 48px; letter-spacing: 10px;
    color: var(--purple);
    line-height: 1;
  }
  .details {
    position: absolute; left: 0; right: 0; top: 196px;
    display: flex; justify-content: center;
  }
  .person {
    text-align: right; padding-right: 16px;
    border-right: 1px solid #b9b9b9;
    color: var(--ink); font-size: 13px; line-height: 1.35;
  }
  .person-name { color: var(--purple); font-weight: 700; font-size: 17px; }
  .contact { padding-left: 14px; list-style: none; font-size: 13px; color: var(--ink); line-height: 1.75; }
  .contact li { display: flex; align-items: center; gap: 6px; }
  .contact svg { width: 13px; height: 13px; flex: none; }

  /* Back */
  .card-back { padding: 40px 46px 0; color: var(--ink); }
  .appt-title {
    text-align: center; color: var(--purple);
    font-weight: 700; font-size: 15px; letter-spacing: .3px;
    margin-bottom: 28px;
  }
  .field-row { display: flex; align-items: flex-end; gap: 8px; font-size: 14px; margin-bottom: 24px; }
  .field-line { flex: 1; border-bottom: 1px solid #9a9a9a; height: 1px; margin-bottom: 4px; }
  .field-line.short { flex: .8; }
  .hours { text-align: center; font-size: 14px; line-height: 1.5; margin-top: 6px; }
  .notice { text-align: center; font-style: italic; color: var(--ink-light); font-size: 14px; margin-top: 22px; }
</style>
</head>
<body>
<main class="sheet">

  <section class="card card-front" aria-label="Business card front">
    <div class="band"></div>
    <h1 class="brand-name">LUMO</h1>
    <div class="details">
      <div class="person">
        <div class="person-name">Your Name</div>
        <div>Title</div>
        <div>1480 E Alder St, Denver</div>
        <div>CO 80206</div>
      </div>
      <ul class="contact">
        <li>
          <svg viewBox="0 0 16 16" aria-hidden="true"><circle cx="8" cy="8" r="8" fill="var(--purple)"/><path d="M5.3 4.2l1.4 1.6-.7 1c.5 1.1 1.2 1.8 2.3 2.3l1-.7 1.6 1.4-.8 1.3c-2.8-.3-5.2-2.7-5.5-5.5z" fill="#fff"/></svg>
          303.555.0148
        </li>
        <li>
          <svg viewBox="0 0 16 16" aria-hidden="true"><circle cx="8" cy="8" r="8" fill="var(--purple)"/><rect x="4" y="5" width="8" height="6" fill="#fff"/><path d="M4 5l4 3.2L12 5" stroke="var(--purple)" fill="none" stroke-width="1"/></svg>
          info@lumobodyworkofdenver.example
        </li>
        <li>
          <svg viewBox="0 0 16 16" aria-hidden="true"><circle cx="8" cy="8" r="8" fill="var(--purple)"/><g fill="none" stroke="#fff" stroke-width="1"><circle cx="8" cy="8" r="4.2"/><ellipse cx="8" cy="8" rx="1.8" ry="4.2"/><path d="M3.8 8h8.4"/></g></svg>
          www.lumobodyworkofdenver.example
        </li>
      </ul>
    </div>
  </section>

  <section class="card card-back" aria-label="Business card back">
    <h2 class="appt-title">YOUR APPOINTMENT</h2>
    <div class="field-row">
      <span>Name :</span><span class="field-line short"></span>
      <span>Time :</span><span class="field-line short"></span>
      <span>am / pm</span>
    </div>
    <div class="field-row">
      <span>Date :</span><span class="field-line"></span>
    </div>
    <p class="hours">Tues - Fri 10am - 8pm | Sat 10am-5pm<br>(Appointments required) No walk-ins please.</p>
    <p class="notice">We appreciate a 24 hr. notice for cancellations</p>
  </section>

</main>
</body>
</html>
```